Heron Loan Partners Business Card

We need a business card design for our mortgage servicing company. In addition to servicing the loans of homeowners, we help homeowners with purchasing their homes and any mortgage refinancing. We would like to see designs that use the colors in the logo attached below (gold-ish yellow and navy blue), and any other design you deem fit! The design should communicate a simpler life with smart mortgages provided by Heron.

```html
<!DOCTYPE html>
<html lang="en">
<head>
<meta charset="utf-8">
<title>Heron Loan Partners Business Card</title>
<link href="https://fonts.googleapis.com/css2?family=Montserrat:wght@400;500;700&display=swap" rel="stylesheet">
<style>
  :root {
    --backdrop: #474747;
    --gold: #e0b33f;
    --navy: #231f52;
    --paper: #ffffff;
    --ink: #1a1a1a;
  }
  * { box-sizing: border-box; margin: 0; padding: 0; }
  html, body {
    width: 1200px; height: 1200px; overflow: hidden;
    background: var(--backdrop);
    font-family: "Montserrat", sans-serif;
  }
  .card {
    position: absolute;
    left: 193px;
    width: 818px;
    height: 463px;
    border-radius: 26px;
    overflow: hidden;
  }
  .card--front { top: 175px; background: var(--paper); }
  .card--back { top: 685px; background: var(--gold); }

  .holder { position: absolute; left: 46px; top: 70px; }
  .holder__name {
    font-size: 23px; font-weight: 700; letter-spacing: 0.2px;
    color: var(--navy); line-height: 1;
  }
  .holder__name span { color: var(--gold); }
  .holder__role { font-size: 19px; font-weight: 400; color: var(--ink); margin-top: 10px; }

  .brand-mark {
    position: absolute; left: 409px; top: 78px; width: 354px;
    text-align: center;
    font-size: 29px; font-weight: 700; color: var(--gold); line-height: 1.1;
  }

  .contacts { position: absolute; left: 44px; top: 270px; list-style: none; }
  .contacts li {
    display: flex; align-items: center; gap: 11px;
    height: 32.5px; font-size: 18.5px; color: var(--ink);
  }
  .contacts svg { width: 21px; height: 21px; flex: none; }

  .address {
    position: absolute; left: 535px; top: 292px;
    font-size: 18.5px; line-height: 29px; color: var(--ink);
  }

  .wave { position: absolute; left: 0; top: 0; width: 818px; height: 463px; }

  .brand-mark--large {
    position: absolute; left: 0; right: 0; top: 200px;
    text-align: center;
    font-size: 50px; font-weight: 700; color: var(--paper); line-height: 1.1;
  }
</style>
</head>
<body>

<section class="card card--front">
  <svg class="wave" viewBox="0 0 818 463" aria-hidden="true">
    <path d="M0 378 C80 400 150 418 230 416 C380 410 520 384 640 386 C720 388 780 405 818 419 L818 463 L0 463 Z" fill="var(--gold)"/>
    <path d="M0 375 C70 395 140 409 230 408 C380 404 510 369 640 368 C720 368 780 390 818 409 L818 402 C780 383 720 364 640 364 C510 364 380 398 230 401 C140 402 70 389 0 371 Z" fill="var(--navy)"/>
  </svg>

  <div class="holder">
    <p class="holder__name">DANA <span>WHITFIELD</span></p>
    <p class="holder__role">Owner</p>
  </div>

  <p class="brand-mark">Heron Loan Partners</p>

  <ul class="contacts">
    <li>
      <svg viewBox="0 0 24 24" aria-hidden="true"><path fill="var(--gold)" d="M3 9c0-3 4-5 9-5s9 2 9 5v2h-5V8.5C14.5 8 9.5 8 8 8.5V11H3z M6 12h12l2 8H4z"/></svg>
      317.555.0142
    </li>
    <li>
      <svg viewBox="0 0 24 24" aria-hidden="true"><rect x="2" y="5" width="20" height="14" fill="var(--gold)"/><path d="M2 5l10 8 10-8M2 19l8-7M22 19l-8-7" stroke="var(--paper)" stroke-width="1.5" fill="none"/></svg>
      info@heronloanpartners.com
    </li>
    <li>
      <svg viewBox="0 0 24 24" aria-hidden="true"><circle cx="12" cy="12" r="10" fill="var(--gold)"/><path d="M7 7c2 1 3 3 2 5s1 4 0 6M14 5c-1 2 1 3 3 3s3 3 1 5" stroke="var(--paper)" stroke-width="1.6" fill="none"/></svg>
      www.heronloanpartners.com
    </li>
  </ul>

  <p class="address">2480 Cedar Ridge Ave, Ste<br>100, Dallas, TX 75201</p>
</section>

<section class="card card--back">
  <p class="brand-mark--large">Heron Loan Partners</p>
</section>

</body>
</html>
```